BOLD & MINIMALIST DESIGN NEEDED

We want a very bold but minimalistic business card design that is impactful and utilizes both sides of the business card. Our current logo is included for your use.

We want bold fonts and good use of negative space. We don't want the logo to overpower the design.

Target Market(s)

Professionals who are building new commercial buildings.

Industry/Entity Type

Construction

Contact Information for Business Card

Name, Title, email, office phone, cell phone, website

Font styles to use
Serif
Sans Serif

Requirements
Must have
• Bold design!

```html
<!DOCTYPE html>
<html lang="en">
<head>
<meta charset="utf-8">
<title>Ridgeline Business Card</title>
<link href="https://fonts.googleapis.com/css2?family=Archivo:wght@400;800&family=Arimo:wght@400;700&display=swap" rel="stylesheet">
<style>
  :root {
    --backdrop: #7a7a7a;
    --card-white: #f3f3f4;
    --green-light: #acd478;
    --green-deep: #7ab826;
    --ink: #111111;
  }
  * { box-sizing: border-box; margin: 0; padding: 0; }
  html, body { width: 1200px; height: 900px; overflow: hidden; }
  body {
    background: var(--backdrop);
    position: relative;
    font-family: "Arimo", Arial, sans-serif;
    color: var(--ink);
  }
  .card {
    position: absolute;
    width: 560px;
    height: 320px;
    border-radius: 22px;
    box-shadow: 0 6px 14px rgba(0,0,0,0.35);
  }
  .card-front {
    left: 150px;
    top: 80px;
    background: var(--card-white);
    display: flex;
    align-items: center;
    justify-content: center;
  }
  .brand-name {
    font-family: "Archivo", Arial, sans-serif;
    font-weight: 800;
    font-size: 62px;
    letter-spacing: 1px;
    color: var(--ink);
  }
  .card-back {
    left: 490px;
    top: 500px;
    background: radial-gradient(ellipse at 50% 50%, var(--green-light) 0%, var(--green-deep) 80%);
    display: flex;
    align-items: center;
    justify-content: center;
    gap: 22px;
  }
  .identity {
    text-align: right;
    padding-top: 30px;
  }
  .person-name {
    font-family: "Archivo", Arial, sans-serif;
    font-weight: 800;
    font-size: 24px;
    line-height: 1;
  }
  .person-title {
    font-size: 15px;
    margin-top: 2px;
  }
  .divider {
    width: 1.5px;
    height: 110px;
    background: var(--ink);
  }
  .contact {
    font-size: 14px;
    line-height: 1.3;
  }
  .contact .address { margin-bottom: 12px; }
  .label { font-weight: 700; }
  .email-line {
    font-size: 14px;
    margin-top: 28px;
    text-align: right;
  }
</style>
</head>
<body>
  <section class="card card-front" aria-label="Card front">
    <span class="brand-name">RIDGELINE</span>
  </section>

  <section class="card card-back" aria-label="Card back">
    <div class="identity">
      <div class="person-name">OWEN CARTER</div>
      <div class="person-title">President</div>
      <div class="email-line"><span class="label">E :</span> hello@ridgelinebuild.com</div>
    </div>
    <div class="divider"></div>
    <div class="contact">
      <div class="address">4120 Harborview Lane<br>Cedar Grove, NY 11020</div>
      <div><span class="label">P :</span> (555) 0142-7788</div>
      <div><span class="label">W :</span> www.ridgelinebuild.com</div>
    </div>
  </section>
</body>
</html>
```